SkyvornQ Business Cards and Stationary Design

Need a design for our business cards and stationary. I want to carry on the theme of the logo. I want the business cards to have a design on the back. I would like the business cards and the stationary to carry the same theme, design scheme, and branding

Target Market(s)

Airlines and Maintenance Facilities

Industry/Entity Type

Aviation

Contact Information for Business Card

Name
Position Title
Address: 4827 Trellis Hollow Road, Fort Pierce, Florida, 34951
Office Number
Mobile Number
Email
Website

Font styles to use
Serif
Sans Serif

Colors

Designer to choose colors to be used in the design.

```html
<!DOCTYPE html>
<html lang="en">
<head>
<meta charset="utf-8">
<title>SkyvornQ Business Card</title>
<link rel="stylesheet" href="https://fonts.googleapis.com/css2?family=Michroma&family=Source+Sans+3:wght@400;600;700&display=swap">
<style>
  :root {
    --bg: #e9ebee;
    --navy: #0b2a55;
    --sky: #0aa3e8;
    --blue-deep: #0a4f9c;
    --blue-light: #1487d8;
    --white: #ffffff;
  }
  * { margin: 0; padding: 0; box-sizing: border-box; }
  html, body { width: 1200px; height: 872px; overflow: hidden; background: var(--bg); }
  .canvas {
    width: 1200px; height: 872px;
    display: flex; flex-direction: column; align-items: center; justify-content: center; gap: 24px;
  }
  .card {
    position: relative; width: 700px; height: 400px; overflow: hidden;
    box-shadow: 0 6px 18px rgba(0,0,0,.18);
    font-family: "Source Sans 3", sans-serif;
  }
  /* Back side */
  .card-back {
    background: radial-gradient(ellipse at 50% 45%, var(--blue-light) 0%, var(--blue-deep) 75%);
  }
  .back-brand {
    position: absolute; top: 150px; left: 0; width: 100%;
    display: flex; align-items: center; justify-content: center; gap: 18px;
  }
  .back-brand .mark { width: 64px; height: 64px; border-radius: 50%; background: var(--navy); opacity: .55; }
  .back-brand .name {
    font-family: "Michroma", sans-serif; font-size: 40px; letter-spacing: 6px;
    color: var(--navy); opacity: .7; white-space: nowrap;
  }
  .back-web {
    position: absolute; bottom: 42px; right: 60px;
    color: var(--white); font-size: 20px; letter-spacing: 4px;
  }
  /* Front side */
  .card-front { background: var(--white); }
  .band { position: absolute; inset: 0; }
  .brand-mark {
    position: absolute; top: 48px; left: 196px; width: 82px; height: 82px;
    border-radius: 50%; background: var(--sky);
  }
  .brand-name {
    position: absolute; top: 152px; left: 52px; white-space: nowrap;
    font-family: "Michroma", sans-serif; font-size: 33px; font-weight: 400;
    letter-spacing: 5px; line-height: 1.2; color: var(--navy);
  }
  .name-tag {
    position: absolute; top: 178px; left: 452px; width: 222px; height: 70px;
    background: var(--sky); border-radius: 16px 36px 16px 36px;
    color: var(--white); text-align: center; padding-top: 10px;
  }
  .name-tag .person { font-size: 24px; font-weight: 700; line-height: 1.1; white-space: nowrap; }
  .name-tag .role { font-size: 19px; font-weight: 400; line-height: 1.2; }
  .contacts {
    position: absolute; top: 284px; left: 40px; list-style: none; color: var(--white); font-size: 18px;
  }
  .contacts li { display: flex; align-items: center; gap: 8px; height: 26px; }
  .contacts svg { width: 16px; height: 16px; flex: none; }
  .divider { position: absolute; top: 300px; left: 300px; width: 1px; height: 60px; background: rgba(255,255,255,.4); }
  .address {
    position: absolute; top: 290px; left: 322px; display: flex; gap: 8px;
    color: var(--white); font-size: 18px; line-height: 1.35;
  }
  .address svg { width: 16px; height: 16px; margin-top: 3px; flex: none; }
</style>
</head>
<body>
<main class="canvas">
  <section class="card card-back" aria-label="Card back">
    <div class="back-brand">
      <span class="mark"></span>
      <span class="name">SKYVORNQ</span>
    </div>
    <p class="back-web">www.skyvornq.com</p>
  </section>

  <section class="card card-front" aria-label="Card front">
    <svg class="band" viewBox="0 0 700 400" aria-hidden="true">
      <path d="M0 262 H410 C450 262 452 206 500 206 H700 V400 H0 Z" fill="var(--navy)"/>
    </svg>
    <span class="brand-mark"></span>
    <h1 class="brand-name">SKYVORNQ</h1>
    <div class="name-tag">
      <p class="person">MARLOW TEAGUE</p>
      <p class="role">PRESIDENT</p>
    </div>

    <ul class="contacts">
      <li>
        <svg viewBox="0 0 16 16" fill="none" stroke="#fff" stroke-width="1.3"><circle cx="8" cy="8" r="7"/><path d="M5.5 4.5l1.5 1.5-1 1c.6 1.2 1.6 2.2 2.8 2.8l1-1 1.5 1.5-1 1c-2.8-.5-5.3-3-5.8-5.8z" fill="#fff" stroke="none"/></svg>
        021-438-5607
      </li>
      <li>
        <svg viewBox="0 0 16 16" fill="none" stroke="#fff" stroke-width="1.3"><circle cx="8" cy="8" r="7"/><rect x="5.8" y="4" width="4.4" height="8" rx="1"/></svg>
        021-438-5607
      </li>
      <li>
        <svg viewBox="0 0 16 16" fill="none" stroke="#fff" stroke-width="1.3"><circle cx="8" cy="8" r="7"/><rect x="4.5" y="5.5" width="7" height="5"/><path d="M4.5 5.5L8 8.5l3.5-3"/></svg>
        info@skyvornq.com
      </li>
      <li>
        <svg viewBox="0 0 16 16" fill="none" stroke="#fff" stroke-width="1.3"><circle cx="8" cy="8" r="7"/><ellipse cx="8" cy="8" rx="3" ry="7"/><path d="M1 8h14"/></svg>
        www.skyvornq.com
      </li>
    </ul>
    <span class="divider"></span>
    <div class="address">
      <svg viewBox="0 0 16 16" fill="none" stroke="#fff" stroke-width="1.3"><circle cx="8" cy="8" r="7"/><path d="M8 12s-3-3-3-5a3 3 0 016 0c0 2-3 5-3 5z"/></svg>
      <p>4827 Trellis Hollow Road,<br>Fort Pierce, Florida, 34951</p>
    </div>
  </section>
</main>
</body>
</html>
```